Landingpage Design X-Mas Invitation

Every year we invite customers to a special X-Mas Apéro. Since we are an IT-Company we handle the registration process by a landingpage. For this we need a design for the event 2016. The content will be the same as 2015 (you will finde the design attached from last year. There will be an additional job for creating the E-Mail.

Target Market(s)

Customers of IT Company, medium Companys in Central Switzerland

Industry/Entity Type

It Company

Number of Pages Required

1 page

Requirements
Must have
• Christmas Style

```html
<!DOCTYPE html>
<html lang="de">
<head>
<meta charset="utf-8">
<title>Lichtwerk – Weihnachts-Apéro Anmeldung</title>
<link rel="stylesheet" href="https://fonts.googleapis.com/css2?family=Lato:ital,wght@1,400&family=Roboto:wght@400;500&display=swap">
<style>
  :root {
    --brand-red: #c8452f;
    --text-white: #ffffff;
    --text-dark: #333333;
    --hero-black: #050403;
    --warm-1: #9a5a14;
    --warm-2: #5a2e0c;
    --warm-3: #2a1606;
    --partner-border: #e2e2e2;
    --badge-grey: #bdbdbd;
    --footer-bg: #232323;
  }
  * { box-sizing: border-box; margin: 0; padding: 0; }
  html, body { width: 1200px; height: 1161px; overflow: hidden; }
  body { font-family: "Roboto", Arial, sans-serif; background: #fff; position: relative; }

  .site-header {
    position: absolute; left: 0; top: 0; width: 1200px; height: 113px;
    border-top: 3px solid var(--brand-red); background: #fff;
  }
  .brand {
    position: absolute; left: 0; width: 1200px; top: 36px;
    display: flex; justify-content: center; align-items: center; gap: 12px;
  }
  .brand-mark { width: 14px; height: 14px; background: var(--text-dark); }
  .brand-name {
    font-family: "Roboto", Arial, sans-serif; font-weight: 500; font-size: 30px;
    color: var(--text-dark); line-height: 36px;
  }

  .hero {
    position: absolute; left: 0; top: 113px; width: 1200px; height: 788px;
    background: var(--hero-black); overflow: hidden;
  }
  .hero-visual {
    position: absolute; inset: 0;
    background:
      radial-gradient(ellipse 330px 300px at 200px 300px, rgba(200,120,30,0.75), transparent 70%),
      radial-gradient(ellipse 420px 420px at 250px 620px, rgba(120,70,20,0.6), transparent 75%),
      linear-gradient(90deg, var(--warm-1) 0%, var(--warm-2) 28%, var(--warm-3) 48%, var(--hero-black) 62%);
  }
  .invite {
    position: absolute; left: 616px; top: 78px; width: 500px; color: var(--text-white);
  }
  .invite p { font-size: 16px; line-height: 22px; margin-bottom: 22px; }
  .section-title {
    font-family: "Lato", Arial, sans-serif; font-style: italic; font-weight: 400;
    font-size: 23px; margin: 0 0 14px;
  }
  .field {
    height: 39px; border: 2px solid var(--text-white); border-radius: 20px;
    padding-left: 26px; font-size: 13px; line-height: 35px; color: var(--text-white);
    margin-bottom: 12px;
  }
  .field-wide { width: 494px; }
  .field-row { display: flex; gap: 17px; }
  .field-row .field { width: 238px; }
  .guest-title { margin-top: 48px; }
  .actions { margin-top: 40px; padding-left: 2px; }
  .action-link {
    display: block; color: var(--text-white); font-size: 21px; font-weight: 500;
    text-decoration: underline; line-height: 28px;
  }

  .partners {
    position: absolute; left: 0; top: 901px; width: 1200px; height: 178px; background: #fff;
  }
  .partner {
    position: absolute; top: 42px; width: 154px; height: 94px;
    border: 1px solid var(--partner-border);
    display: flex; align-items: center; justify-content: center;
  }
  .partner-badge { width: 44px; height: 44px; border-radius: 50%; background: var(--badge-grey); }

  .site-footer {
    position: absolute; left: 0; top: 1079px; width: 1200px; height: 82px;
    background: var(--footer-bg); color: var(--text-white);
    font-size: 14px; text-align: center; line-height: 82px;
  }
</style>
</head>
<body>
  <header class="site-header">
    <div class="brand">
      <span class="brand-mark"></span>
      <span class="brand-name">Lichtwerk</span>
    </div>
  </header>

  <section class="hero">
    <div class="hero-visual" role="img" aria-label="Weihnachtskugel mit Schneeflocke vor bunten, unscharfen Lichterketten"></div>
    <div class="invite">
      <p>Ob Sie den ganzen Abend bleiben oder nur kurz nach dem Weihnachts-Shopping vorbeischauen, ist ganz Ihnen überlassen.</p>
      <p>Wir freuen uns sehr, wenn Sie uns die Gelegenheit geben, Ihnen mit dieser Einladung für die<br><br>erfolgreiche Zusammenarbeit herzlichst zu danken.</p>

      <h2 class="section-title" style="margin-top:40px">Ihre Anmeldung</h2>
      <div class="field field-wide">Ihre E-mail-Adresse</div>
      <div class="field-row">
        <div class="field">Vorname</div>
        <div class="field">Nachname</div>
      </div>

      <h2 class="section-title guest-title">Ihre Begleitperson</h2>
      <div class="field field-wide">Firma (Optional)</div>
      <div class="field-row">
        <div class="field">Vorname</div>
        <div class="field">Nachname</div>
      </div>

      <div class="actions">
        <span class="action-link">Weitere Begleitperson</span>
        <span class="action-link">Absenden</span>
      </div>
    </div>
  </section>

  <section class="partners" aria-label="Partner">
    <div class="partner" style="left:73px"><span class="partner-badge"></span></div>
    <div class="partner" style="left:253px"><span class="partner-badge"></span></div>
    <div class="partner" style="left:433px"><span class="partner-badge"></span></div>
    <div class="partner" style="left:613px"><span class="partner-badge"></span></div>
    <div class="partner" style="left:793px"><span class="partner-badge"></span></div>
    <div class="partner" style="left:973px"><span class="partner-badge"></span></div>
  </section>

  <footer class="site-footer">Copyright ©, Lichtwerk.&nbsp; All Rights Reserved.</footer>
</body>
</html>
```